Tidewell Health & Wellness Center Remedium

BluSketcho, Submit your previous card design as well as a couple others. Challenge yourself to make it great! You know what I want.
Updates

I would like to have a Chatterly logo beside my logo

Some designers are putting my information on the cards, but a lot are not using the information I have supplied. WHY?

I would to seed some designs on a BLACK background please, thank you.

Please include my titles "PharmD. RpH CuraLink" beside or under my name.

Industry/Entity Type

Health

Colors
add136

Requirements
Must have
• Tidewell Health & Wellness Center
Founder & President | Lou Pemberg
Coral Inlet Marlin State, 40417
239-555-0187
Nice to have
• I would like to have a Chatterly logo and Tidewell Health & Wellness Remedium

```html
<!DOCTYPE html>
<html lang="en">
<head>
<meta charset="utf-8">
<title>Tidewell Health &amp; Wellness Center Remedium – Business Card</title>
<link rel="stylesheet" href="https://fonts.googleapis.com/css2?family=Libre+Baskerville&display=swap">
<style>
  :root {
    --page-bg: #e9e9e7;
    --card-white: #ffffff;
    --brand-green: #2f8f2c;
    --brand-green-deep: #3f8f32;
    --brand-green-light: #9ccb62;
    --leaf-dark: #3f9a2e;
    --leaf-light: #a7d66b;
    --ink-light: #ffffff;
    --card-shadow: rgba(0, 0, 0, 0.18);
  }
  * { box-sizing: border-box; margin: 0; padding: 0; }
  html, body {
    width: 1200px; height: 1200px; overflow: hidden;
    background: var(--page-bg);
    font-family: "Libre Baskerville", Georgia, serif;
  }
  .sheet {
    position: relative; width: 1200px; height: 1200px;
    display: flex; flex-direction: column; align-items: center; justify-content: center; gap: 44px;
  }
  .card {
    position: relative; width: 900px; height: 514px;
    box-shadow: 0 8px 24px var(--card-shadow);
    overflow: hidden;
  }

  /* Front */
  .card--front { background: var(--card-white); }
  .leaf-cluster {
    position: absolute; width: 150px; height: 130px;
    background: radial-gradient(ellipse at center, var(--leaf-light) 0%, var(--leaf-dark) 60%, rgba(63,154,46,0) 72%);
  }
  .leaf-cluster--top-left { left: -10px; top: -20px; }
  .leaf-cluster--mid-left { left: -30px; top: 250px; }
  .leaf-cluster--top-right { right: -20px; top: 120px; }
  .leaf-cluster--bottom-right { right: -10px; bottom: -20px; width: 180px; height: 160px; }
  .front-brand {
    position: absolute; left: 0; right: 0; top: 70px;
    display: flex; flex-direction: column; align-items: center; color: var(--brand-green);
  }
  .brand-circle { width: 170px; height: 170px; }
  .front-brand .brand-name { font-size: 72px; line-height: 1; margin-top: 18px; }
  .front-brand .brand-tagline { font-size: 21px; margin-top: 8px; }

  /* Back */
  .card--back {
    background: radial-gradient(ellipse 55% 60% at 45% 40%, var(--brand-green-light) 0%, #6cae47 45%, var(--brand-green-deep) 100%);
    color: var(--ink-light);
  }
  .back-brand { position: absolute; left: 0; right: 0; top: 34px; text-align: center; }
  .back-brand .brand-name { font-size: 76px; line-height: 1; }
  .back-brand .brand-tagline { font-size: 21px; margin-top: 6px; }
  .contact-block {
    position: absolute; top: 196px; left: 0; right: 0;
    display: flex; justify-content: center;
  }
  .person { text-align: right; padding-right: 26px; }
  .person__name { font-size: 44px; letter-spacing: 1px; line-height: 1.1; }
  .person__role, .person__titles { font-size: 21px; line-height: 1.5; }
  .divider { width: 2px; background: var(--ink-light); }
  .details { padding-left: 26px; padding-top: 8px; font-size: 22px; line-height: 1.45; }
  .details .email { font-size: 19px; }
  .social {
    position: absolute; left: 0; right: 0; bottom: 48px;
    display: flex; justify-content: center; align-items: center; gap: 14px;
    font-size: 24px;
  }
  .social__square { width: 34px; height: 34px; background: var(--ink-light); }
</style>
</head>
<body>
<main class="sheet">

  <section class="card card--front" aria-label="Card front">
    <div class="leaf-cluster leaf-cluster--top-left" role="img" aria-label="Green leaf illustration"></div>
    <div class="leaf-cluster leaf-cluster--mid-left" role="img" aria-label="Green leaf illustration"></div>
    <div class="leaf-cluster leaf-cluster--top-right" role="img" aria-label="Green leaf illustration"></div>
    <div class="leaf-cluster leaf-cluster--bottom-right" role="img" aria-label="Green leaf illustration"></div>
    <div class="front-brand">
      <svg class="brand-circle" viewBox="0 0 170 170" aria-hidden="true">
        <circle cx="85" cy="85" r="78" fill="none" stroke="var(--brand-green)" stroke-width="6"/>
      </svg>
      <div class="brand-name">Tidewell</div>
      <div class="brand-tagline">Health &amp; Wellness Center Remedium</div>
    </div>
  </section>

  <section class="card card--back" aria-label="Card back">
    <header class="back-brand">
      <div class="brand-name">Tidewell</div>
      <div class="brand-tagline">Health &amp; Wellness Center Remedium</div>
    </header>
    <div class="contact-block">
      <div class="person">
        <div class="person__name">LOU PEMBERG</div>
        <div class="person__role">President &amp; Founder</div>
        <div class="person__titles">PharmD., R.Ph, CuraLink</div>
      </div>
      <div class="divider"></div>
      <div class="details">
        <div>239-555-0187</div>
        <div>Coral Inlet</div>
        <div>Marlin State, 40417</div>
        <div class="email">loupemberg01@postnest.com</div>
      </div>
    </div>
    <div class="social">
      <span class="social__square" aria-hidden="true"></span>
      <span>Chatterly · Tidewell Health &amp; Wellness</span>
    </div>
  </section>

</main>
</body>
</html>
```